Design a website for our small self storage business

We're looking for a freelance web designer who can produce a good-looking design for our small business website (no coding necessary). We will provide a list of pages to design, along with content outlines.

Key skills:
- Graphic design
- Responsive web design
- Proficiency with a modern web design tool such as Figma, Adobe Xd, or InVision

Please send relevant previous work (preferably in an inspectable format such as Figma or Invision).

```html
<!DOCTYPE html>
<html lang="en">
<head>
<meta charset="utf-8">
<title>Bayside Self Storage</title>
<link href="https://fonts.googleapis.com/css2?family=Roboto:ital,wght@0,400;0,500;0,700;1,400&display=swap" rel="stylesheet">
<style>
:root{
  --navy:#0f4c8a;
  --blue:#1f5a99;
  --red:#e31e24;
  --ink:#111;
  --text:#555;
  --pale:#f3f6fb;
  --footer:#111;
  --star:#f5b400;
}
*{box-sizing:border-box;margin:0;padding:0}
html,body{width:1200px;height:3787px;overflow:hidden}
body{font-family:'Roboto',sans-serif;color:var(--ink);background:#fff;position:relative}
section,header,footer{position:absolute;left:0;width:1200px}
.abs{position:absolute}
.btn{position:absolute;background:var(--red);color:#fff;font-weight:700;font-size:16px;text-transform:uppercase;display:flex;align-items:center;justify-content:center;border-radius:3px}
.para{font-size:15px;line-height:28.3px;color:var(--text)}
.h2{font-size:38px;font-weight:700;text-transform:uppercase;line-height:42px}
.rule{display:inline-block;width:64px;height:3px;background:var(--navy);vertical-align:middle}

/* header */
.topbar{top:0;height:42px;background:var(--navy)}
.topbar .white{position:absolute;left:0;top:0;width:330px;height:42px;background:#fff;clip-path:polygon(0 0,280px 0,330px 42px,0 42px)}
.topbar .info{position:absolute;top:12px;color:#fff;font-size:14px;font-weight:500}
.header{top:42px;height:73px;background:#fff}
.logo{position:absolute;left:110px;top:-38px;width:160px;text-align:center;color:var(--navy)}
.logo .mark{width:30px;height:30px;background:var(--red);margin:0 auto 2px}
.logo .name{font-size:28px;font-weight:500;line-height:28px;letter-spacing:1px}
.logo .sub{font-size:14px;font-weight:500;letter-spacing:1.5px;line-height:15px}
.logo .sub.red{color:var(--red)}
.nav a{position:absolute;top:30px;font-size:16px;font-weight:500;color:var(--ink);text-decoration:none}
.nav a.active{color:var(--red)}
.nav a.active::after{content:"";position:absolute;left:0;right:0;bottom:-6px;height:2px;background:var(--red)}

/* hero */
.hero{top:115px;height:616px}
.hero .photo{position:absolute;inset:0;background:linear-gradient(90deg,#6f9a3c 0%,#a8cf4a 25%,#d9dcd6 48%,#b39a73 62%,#d6dbcf 80%,#8fb04a 100%)}
.hero h1{position:absolute;left:110px;top:178px;font-size:56px;line-height:54px;color:#fff;font-weight:700}
.hero p{position:absolute;left:113px;top:303px;width:400px;font-size:15px;line-height:27px;color:#fff;font-weight:500}
.arrow{position:absolute;top:285px}
.dots{position:absolute;left:548px;top:582px;display:flex;gap:18px}
.dots i{width:10px;height:10px;border-radius:50%;background:rgba(255,255,255,.5)}
.dots i.on{background:#fff}

/* welcome */
.welcome{top:731px;height:567px;background:linear-gradient(180deg,#fff 0%,#fff 40%,#dfe6ea 55%,#6f7f7a 75%,#4c5a55 100%)}
.welcome .photo{position:absolute;left:0;right:0;bottom:0;height:300px;background:linear-gradient(180deg,rgba(255,255,255,0) 0%,#8a9a8e 35%,#5c6e66 70%,#4d5651 100%)}
.welcome .title{position:absolute;top:78px;left:0;width:1200px;text-align:center;font-size:31px;font-weight:700}
.welcome .title .rule{margin:0 10px}
.welcome .para{position:absolute;left:154px;width:892px;top:123px;text-align:center;font-size:14px}

/* split rows */
.split{height:556px}
.split .photo{position:absolute;top:0;width:600px;height:100%}
.split .copy{position:absolute;width:450px}
.drive{top:1298px;background:var(--pale)}
.drive .photo{left:0;background:linear-gradient(135deg,#27415f 0%,#c9cfd6 45%,#e5e8ec 60%,#4d6885 85%,#1f3552 100%)}
.show{top:1854px;height:557px;background:var(--pale)}
.show .photo{left:600px;background:radial-gradient(ellipse at 50% 55%,#bfae8a 0%,#6f6f70 30%,#2a4ea8 48%,#d8d8d6 60%,#c4c4c2 100%)}

/* testimonials */
.testi{top:2411px;height:554px;background:#fff}
.testi .title{position:absolute;top:76px;width:1200px;text-align:center;font-size:38px;font-weight:700}
.testi .title .rule{margin:0 16px}
.card{position:absolute;top:155px;width:466px;height:230px;border:1px solid #e5e5e5;box-shadow:0 4px 10px rgba(0,0,0,.06);padding:26px 24px}
.card .q{font-size:44px;color:#888;font-family:Georgia,serif;line-height:30px;display:inline-block;vertical-align:top}
.card .stars{display:inline-block;color:var(--star);font-size:22px;letter-spacing:2px;margin-left:14px;vertical-align:top}
.card p{margin-top:14px;font-style:italic;font-size:15px;line-height:28.3px;color:var(--text)}
.person{position:absolute;top:417px;display:flex;align-items:center;gap:18px}
.person .av{width:62px;height:62px;border-radius:50%;background:linear-gradient(135deg,#9aa6ad,#4b5358)}
.person b{display:block;font-size:18px;font-weight:500;color:#222}
.person span{font-size:13px;color:#555}

/* contact */
.contact{top:2965px;height:475px}
.contact .left{position:absolute;left:0;top:0;width:654px;height:100%;background:linear-gradient(90deg,#e7ebef,#f7f8fa 50%,#dfe4ea)}
.contact .right{position:absolute;left:654px;top:0;width:546px;height:100%;background:var(--blue);color:#fff}
.field{position:absolute;background:#fff;font-size:13px;color:#444;padding:0 12px;display:flex;align-items:center}
.field.area{align-items:flex-start;padding-top:16px}
.cinfo{position:absolute;left:46px;display:flex;gap:16px;align-items:center}
.cinfo .ic{width:46px;height:46px;border-radius:50%;background:#fff;display:flex;align-items:center;justify-content:center;flex:none}
.cinfo .t{font-size:15px;line-height:20px}
.cinfo .big{font-size:19px;font-weight:700;letter-spacing:1px}

/* footer */
.footer{top:3440px;height:347px;background:var(--footer);color:#fff}
.footer h4{position:absolute;top:72px;font-size:17px;font-weight:500;text-transform:uppercase}
.footer .links{position:absolute;left:356px;top:118px;font-size:13px;line-height:26px}
.flogo{position:absolute;left:110px;top:60px;width:160px;text-align:center;color:#fff}
.flogo .mark{width:28px;height:28px;background:#fff;margin:0 auto 2px}
.flogo .name{font-size:28px;font-weight:500;letter-spacing:1px;line-height:28px}
.flogo .sub{font-size:14px;letter-spacing:1.5px;line-height:15px}
.social{position:absolute;left:144px;top:188px;display:flex;gap:8px}
.social i{width:26px;height:26px;border-radius:50%;border:1px solid #fff}
.fc{position:absolute;left:532px;font-size:13px;display:flex;gap:12px;align-items:flex-start;line-height:22px}
.fc .dot{width:24px;height:24px;border-radius:50%;background:#2a2a2a;flex:none;display:flex;align-items:center;justify-content:center}
.cards{position:absolute;left:817px;top:222px;display:flex;gap:8px}
.cards i{width:36px;height:22px;background:#fff;border-radius:2px}
.copy-line{position:absolute;left:110px;top:276px;width:980px;border-top:1px solid #333;padding-top:24px;text-align:center;font-size:13px}
</style>
</head>
<body>

<header class="topbar">
  <div class="white"></div>
  <div class="info" style="left:582px">&#9742; +1 888 888 8888</div>
  <div class="abs" style="left:720px;top:8px;width:1px;height:26px;background:#fff"></div>
  <div class="info" style="left:738px">&#9719; Opening Hours: (9:30 AM - 5:30 PM, 7 days a week)</div>
</header>
<header class="header">
  <div class="logo">
    <div class="mark"></div>
    <div class="name">BAYSIDE</div>
    <div class="sub red">SELF STORAGE</div>
    <div class="sub">NORTHGATE</div>
  </div>
  <nav class="nav">
    <a class="active" style="left:463px">HOME</a>
    <a style="left:566px">UNIT SIZES</a>
    <a style="left:707px">SPECIALS</a>
    <a style="left:839px">PAY ONLINE</a>
    <a style="left:988px">CONTACT US</a>
  </nav>
</header>

<section class="hero">
  <div class="photo" role="img" aria-label="Worker moving cardboard boxes on a hand truck in a storage hallway with green doors"></div>
  <h1>BAYSIDE SELF<br>STORAGE</h1>
  <p>Sed ut perspiciatis unde omnis iste natsit voluptatem accusantium doloremque laudantium,</p>
  <div class="btn" style="left:113px;top:381px;width:164px;height:50px">See our units</div>
  <svg class="arrow" style="left:58px" width="24" height="46"><path d="M22 2L3 23l19 21" stroke="#fff" stroke-width="2" fill="none"/></svg>
  <svg class="arrow" style="left:1112px" width="24" height="46"><path d="M2 2l19 21L2 44" stroke="#fff" stroke-width="2" fill="none"/></svg>
  <div class="dots"><i></i><i></i><i class="on"></i><i></i></div>
</section>

<section class="welcome">
  <div class="photo" role="img" aria-label="Long row of outdoor storage units with green roll-up doors"></div>
  <div class="title"><span class="rule"></span>WELCOME TO BAYSIDE SELF STORAGE IN NORTHGATE<span class="rule"></span></div>
  <p class="para">At vero eos et accusamus et iusto odio dignissimos ducimus qui blanditiis praesentium voluptatum deleniti atque corrupti quos dolores et quas molestias excepturi sint occaecati cupiditate non provident, similique sunt in culpa qui officia deserunt mollitia animi, id est laborum et dolorum fuga. Et harum quidem rerum facilis est et expedita distinctio. Nam libero tempore, cum soluta nobis est eligendi optio cumque nihil impedit quo minus id quod maxime placeat facere possimus, omnis voluptas assumenda est, omnis dolor repellendus. Temporibus autem quibusdam et aut officiis debitis aut rerum necessitatibus saepe eveniet ut et voluptates repudiandae sint et molestiae non recusandae. Itaque</p>
  <div class="btn" style="left:517px;top:313px;width:165px;height:51px">Learn more</div>
</section>

<section class="split drive">
  <div class="photo" role="img" aria-label="Indoor storage corridor with blue roll-up doors"></div>
  <div class="copy" style="left:642px;top:84px">
    <div class="h2">DRIVE-UP SPACES <span class="rule"></span></div>
    <p class="para" style="margin-top:20px">At vero eos et accusamus et iusto odioos ducimus qui blanditiis praesentium voluptatum deleniti atque corrupti quos dolores et quas molestias excepturi sint occaecatiupiditate non provident, similique sunt in culpa qui offiaunt mollitia animi, id est laborum et dolorum fuga. Et harum erum facilis est et expedita distinctio. Nam libero tempore, cum soluta bis est eligendi optio cumque nihil impedit quo minus id quod maxie placeat facere possimus, omnis voluptas assumenda est, &nbsp;dolor repellendus. Temporibus autem quibusdam et aut offici debitis aut rerum necessitatibus saepe eveniet ut et voluptates</p>
  </div>
  <div class="btn" style="left:643px;top:453px;width:164px;height:51px">See our units</div>
</section>

<section class="split show">
  <div class="photo" role="img" aria-label="Open storage unit with blue frame holding stacked cardboard boxes"></div>
  <div class="copy" style="left:110px;top:86px">
    <div class="h2">JUST SHOW UP WITH<br>YOUR STUFF <span class="rule"></span></div>
    <p class="para" style="margin-top:14px">At vero eos et accusamus et iusto odioos ducimus qui blanditiis praesentium voluptatum deleniti atque corrupti quos dolores et quas molestias excepturi sint occaecatiupiditate non provident, similique sunt in culpa qui offiaunt mollitia animi, id est laborum et dolorum fuga. Et harum erum facilis est et expedita distinctio. Nam libero tempore, cum soluta bis est eligendi optio cumque nihil impedit quo minus id quod maxie placeat facere possimus, omnis voluptas assumenda est, &nbsp;dolor repellendus. Temporibus autem quibusdam et aut offici</p>
  </div>
  <div class="btn" style="left:110px;top:453px;width:165px;height:51px">See our units</div>
</section>

<section class="testi">
  <div class="title"><span class="rule"></span>CLIENT TESTIMONIALS<span class="rule"></span></div>
  <div class="card" style="left:124px">
    <span class="q">&#8220;</span><span class="stars">&#9733;&#9733;&#9733;&#9733;&#9733;</span>
    <p>Sed ut perspiciatis unde omnis iste natus error sit vo-luptatem accusantium doloremque laudantium, totam rem aperiam, eaque ipsa quae ab illo inventore veritatis et quasi architecto beatae vitae dicta sunt explicabo. Nemo enim ipsam voluptatem quia voluptas sit aspernatur</p>
  </div>
  <div class="card" style="left:611px">
    <span class="q">&#8220;</span><span class="stars">&#9733;&#9733;&#9733;&#9733;&#9733;</span>
    <p>Sed ut perspiciatis unde omnis iste natus errit voluptatem accusantium doloremque laudantium, totam rem aperiam, eaque ipsa quae ab illo ventore veritatis et quasi architecto beatae vitae dicta sxplicabo. Nemo enim ipsam voluptatem quia voluptas s</p>
  </div>
  <div class="person" style="left:124px">
    <div class="av" role="img" aria-label="Client portrait"></div>
    <div><b>Daniel Carver</b><span>CEO, Northfield Partners</span></div>
  </div>
  <div class="person" style="left:611px">
    <div class="av" role="img" aria-label="Client portrait"></div>
    <div><b>Marla Jensen</b><span>CEO Jensen Development</span></div>
  </div>
</section>

<section class="contact">
  <div class="left" role="img" aria-label="Faded storage hallway background"></div>
  <div class="abs" style="left:110px;top:80px;font-size:33px;font-weight:700">GET IN TOUCH</div>
  <div class="abs" style="left:110px;top:124px;width:68px;height:3px;background:var(--navy)"></div>
  <div class="field" style="left:110px;top:145px;width:240px;height:47px">Your Name</div>
  <div class="field" style="left:358px;top:145px;width:240px;height:47px">Email</div>
  <div class="field" style="left:110px;top:200px;width:240px;height:47px">Unit Number</div>
  <div class="field" style="left:358px;top:200px;width:240px;height:47px;justify-content:space-between">Reason for contact<span>&#9662;</span></div>
  <div class="field area" style="left:110px;top:256px;width:488px;height:88px">Message</div>
  <div class="btn" style="left:111px;top:360px;width:163px;height:45px">Submit</div>

  <div class="right">
    <div class="abs" style="left:48px;top:66px;font-size:33px;font-weight:700">CONTACT US</div>
    <p class="abs" style="left:49px;top:116px;width:450px;font-size:15px;font-weight:500;line-height:22px">Sed ut perspiciatis unde onis iste natus error sit voluptatem accusantium doloremque laudantium, totam rem aperiam, eaque ipsa quae ab illo invntore veritatis et quasi architecto beatae vitae dicta sunt explicabo.</p>
    <div class="cinfo" style="top:222px">
      <div class="ic"><svg width="20" height="22" viewBox="0 0 20 22"><path d="M10 1a7 7 0 0 0-7 7c0 5 7 13 7 13s7-8 7-13a7 7 0 0 0-7-7z" fill="#1f5a99"/><circle cx="10" cy="8" r="2.6" fill="#fff"/></svg></div>
      <div class="t">123 Your Adress Goes Here.<br>CA, 1234567</div>
    </div>
    <div class="cinfo" style="top:290px">
      <div class="ic"><svg width="20" height="20" viewBox="0 0 24 24"><path d="M6.6 10.8a15 15 0 0 0 6.6 6.6l2.2-2.2a1 1 0 0 1 1-.25 11.4 11.4 0 0 0 3.6.57 1 1 0 0 1 1 1V20a1 1 0 0 1-1 1A17 17 0 0 1 3 4a1 1 0 0 1 1-1h3.5a1 1 0 0 1 1 1c0 1.25.2 2.45.57 3.57a1 1 0 0 1-.25 1z" fill="#1f5a99"/></svg></div>
      <div class="t">Call Us Today!<br><span class="big">888 888 8888</span></div>
    </div>
    <div class="cinfo" style="top:358px">
      <div class="ic"><svg width="22" height="16" viewBox="0 0 22 16"><rect x="1" y="1" width="20" height="14" rx="1" fill="#1f5a99"/><path d="M1 2l10 7 10-7" stroke="#fff" stroke-width="1.6" fill="none"/></svg></div>
      <div class="t">Email Us<br><span class="big">info@baysideselfstorage.com</span></div>
    </div>
  </div>
</section>

<footer class="footer">
  <div class="flogo">
    <div class="mark"></div>
    <div class="name">BAYSIDE</div>
    <div class="sub">SELF STORAGE</div>
    <div class="sub">NORTHGATE</div>
  </div>
  <div class="social"><i></i><i></i><i></i></div>

  <h4 style="left:356px">Quicik Links</h4>
  <div class="links">Home<br>Unit Sizes<br>Specials<br>Pay Online<br>Contact Us</div>

  <h4 style="left:532px">Contact Us</h4>
  <div class="fc" style="top:118px"><span class="dot"><svg width="10" height="12" viewBox="0 0 20 22"><path d="M10 1a7 7 0 0 0-7 7c0 5 7 13 7 13s7-8 7-13a7 7 0 0 0-7-7z" fill="#fff"/></svg></span><span>123 Your Adress Goes Here.<br>CA, 1234567</span></div>
  <div class="fc" style="top:180px"><span class="dot"><svg width="11" height="11" viewBox="0 0 24 24"><path d="M6.6 10.8a15 15 0 0 0 6.6 6.6l2.2-2.2a1 1 0 0 1 1-.25 11.4 11.4 0 0 0 3.6.57 1 1 0 0 1 1 1V20a1 1 0 0 1-1 1A17 17 0 0 1 3 4a1 1 0 0 1 1-1h3.5a1 1 0 0 1 1 1c0 1.25.2 2.45.57 3.57a1 1 0 0 1-.25 1z" fill="#fff"/></svg></span><span>888 888 8888</span></div>
  <div class="fc" style="top:224px"><span class="dot"><svg width="12" height="9" viewBox="0 0 22 16"><rect x="1" y="1" width="20" height="14" fill="none" stroke="#fff" stroke-width="2"/><path d="M1 2l10 7 10-7" stroke="#fff" stroke-width="2" fill="none"/></svg></span><span>info@baysideselfstorage.com</span></div>

  <h4 style="left:823px">Sign for Newsletter</h4>
  <div class="abs" style="left:820px;top:112px;font-size:12px">Lorem ipsum dolor sit amet, consectetur</div>
  <div class="abs" style="left:817px;top:140px;width:206px;height:42px;background:#fff;color:#666;font-size:13px;padding:13px 15px">Email</div>
  <div class="abs" style="left:1023px;top:140px;width:42px;height:42px;background:var(--blue);display:flex;align-items:center;justify-content:center"><svg width="16" height="16" viewBox="0 0 16 16"><path d="M15 1L1 7l5 2 2 6z" fill="#fff"/></svg></div>
  <div class="cards"><i></i><i></i><i></i><i></i><i></i><i></i></div>

  <div class="copy-line">Copyright &copy; 2022 Bayside Self Storage - All Rights Reserved. Privacy</div>
</footer>

</body>
</html>
```